Larkmoor Drones Business Card

We are a new company based in Central Queensland, Australia that uses specalised drones (Voskel Ferra Q80) to undertake mainly agricultural operations, like spraying weeds, spraying crops, spreading seed etc. I have attached a Plimbo proof of a card I was thinking along the lines of - purely a start point. The drone used in the business card MUST be a Voskel Ferra Q80.
I am very open to other ideas, especially fonts and layout. I don't have website etc set up yet.
The images are stock and easily interchangeable, I just ask that any background images reflect the local central Queensland area. The photo of the drone is not even complete (propellers cut off) and I need a new stock photo – I’m not sure if this is an issue, or I can pay for an image if need be. PLEASE FIND AN FERRA Q80 image - 4 sprayers, not 6.
The logo/business name is very draft and looking for further ideas, ideally incorporating drones or agriculture design elements into the design of the business name. The business name needs work on the graphic/design – it is a draft that I have included, the drone propellers (being a different colour) are DRAFT only and intended for changes. PLEASE DO NOT USE THE DRONE PORPELLER I HAVE USED AS A DRAFT. TRY TO FIND SOMETHING ELSE.. The arrow is a shape and not aligned in any way, I would also like ideas on different fonts and additional elements, like air streams, aviation elements, aviation or country western (farming like) themes and fonts etc.
Ideally looking at staying within the blue, green and yellow colours, keeping with an natural, outdoorsy, environmental feel.

Target Market(s)

Farmers, Agriculture, Local Governments, Land Managers

Industry/Entity Type

Agriculture, Drones, Aviation

Contact Information for Business Card

Agricultural Drone (Voskel Ferra Q80), Farming, Business Name.

Font styles to use
Sans Serif

Colors
0054AA
0677BA
7BADD7
CADEEF
E8F1F8
0094D4
00A9DD
6FCCEA
C7EBF8
E9F6FB
00AB8E
00BBA5
67D7C9
C6EFE9
E9F9F6
59FF00
82FF00
B8FF75
E3FFCB
F4FFEA

Requirements
Must have
• Voskel Ferra Q80 Drone
Should not have
• Tractors

```html
<!DOCTYPE html>
<html lang="en">
<head>
<meta charset="utf-8">
<title>Larkmoor Drones – Business Card</title>
<link rel="stylesheet" href="https://fonts.googleapis.com/css2?family=Archivo:wght@400;500;800;900&family=Marcellus+SC&display=swap">
<style>
  :root {
    --bg: #1d1d1d;
    --card-white: #ffffff;
    --navy: #1f3f8c;
    --navy-deep: #0d2460;
    --ink: #222222;
    --heading-blue: #2d3f7a;
    --drone-grey-light: #eceded;
    --drone-grey-mid: #c9cbcd;
    --sky: #e6eef0;
    --hills: #5f9ea6;
    --field: #3f9a3a;
    --field-deep: #2f7d2c;
  }
  * { box-sizing: border-box; margin: 0; padding: 0; }
  html, body {
    width: 1200px; height: 1059px; overflow: hidden;
    background: var(--bg);
    font-family: "Archivo", sans-serif;
  }
  .card {
    position: absolute;
    left: 258px;
    width: 690px; height: 394px;
    border-radius: 26px;
    overflow: hidden;
    box-shadow: 0 6px 18px rgba(0,0,0,.55);
  }

  /* Front */
  .card--front { top: 93px; background: var(--card-white); }
  .brand {
    position: absolute; left: 0; right: 0; text-align: center;
  }
  .brand__name {
    font-family: "Archivo", sans-serif;
    font-weight: 900;
    font-size: 54px;
    letter-spacing: -1px;
    line-height: 1;
    text-transform: uppercase;
  }
  .brand__tagline {
    font-family: "Marcellus SC", serif;
    font-size: 18px;
    letter-spacing: 2.2px;
    margin-top: 6px;
  }
  .card--front .brand { top: 50px; }
  .card--front .brand__name { color: var(--navy); }
  .card--front .brand__tagline { color: var(--ink); margin-left: -36px; }

  .contacts {
    position: absolute; left: 38px; top: 175px;
    list-style: none;
  }
  .contacts__item {
    display: flex; align-items: center;
    height: 27px; margin-bottom: 0.5px;
    font-size: 17px; color: var(--ink);
    letter-spacing: .3px;
  }
  .contacts__item:last-child { margin-top: 3px; }
  .contacts__icon {
    width: 22px; height: 22px; margin-right: 13px; flex: none;
  }
  .drone-photo {
    position: absolute; left: 322px; top: 166px;
    width: 352px; height: 132px;
    border-radius: 14px;
    background: linear-gradient(180deg, var(--drone-grey-light) 0%, var(--drone-grey-mid) 100%);
  }
  .front-rule {
    position: absolute; left: 0; right: 0; top: 339px;
    height: 3px; background: var(--navy);
  }
  .front-band {
    position: absolute; left: 0; right: 0; top: 346px; bottom: 0;
    background: var(--navy);
    color: #fff; text-align: center;
    font-size: 11.5px; line-height: 14px;
    padding-top: 11px;
  }

  /* Back */
  .card--back { top: 550px; }
  .field-photo {
    position: absolute; inset: 0;
    background: linear-gradient(180deg, var(--sky) 0%, #b9d3d6 10%, var(--hills) 26%, #4f8f8f 45%, var(--field) 62%, var(--field-deep) 100%);
  }
  .services {
    position: absolute; top: 24px; left: 0; right: 0;
    text-align: center;
    font-weight: 900; font-size: 35px;
    color: var(--heading-blue);
    letter-spacing: .3px;
    word-spacing: 6px;
  }
  .back-band {
    position: absolute; left: 0; right: 0; top: 272px; height: 91px;
    background: var(--navy-deep);
  }
  .card--back .brand { top: 284px; }
  .card--back .brand__name { color: #fff; font-size: 48px; }
  .card--back .brand__tagline { color: #fff; font-size: 16px; margin-top: 6px; letter-spacing: 2px; }
</style>
</head>
<body>

<section class="card card--front">
  <div class="brand">
    <div class="brand__name">Larkmoor Drones</div>
    <div class="brand__tagline">SERVICING CENTRAL QUEENSLAND</div>
  </div>

  <ul class="contacts">
    <li class="contacts__item">
      <svg class="contacts__icon" viewBox="0 0 24 24"><circle cx="12" cy="12" r="12" fill="#1f3f8c"/><path d="M8 6.5l2 .2 1 3-1.4 1.1a8 8 0 0 0 3.6 3.6l1.1-1.4 3 1 .2 2c-.6.9-1.6 1.2-2.6 1A10 10 0 0 1 7 9.1c-.2-1 .1-2 1-2.6z" fill="#fff"/></svg>
      123 456 7890
    </li>
    <li class="contacts__item">
      <svg class="contacts__icon" viewBox="0 0 24 24"><circle cx="12" cy="12" r="12" fill="#1f3f8c"/><rect x="6" y="8" width="12" height="8.5" rx="1" fill="#fff"/><path d="M6.5 8.6l5.5 4.2 5.5-4.2" stroke="#1f3f8c" stroke-width="1.4" fill="none"/></svg>
      larkmoordrone@mailnest.com
    </li>
    <li class="contacts__item">
      <svg class="contacts__icon" viewBox="0 0 24 24"><circle cx="12" cy="12" r="12" fill="#1f3f8c"/><circle cx="12" cy="12" r="6.5" fill="none" stroke="#fff" stroke-width="1.4"/><ellipse cx="12" cy="12" rx="2.8" ry="6.5" fill="none" stroke="#fff" stroke-width="1.2"/><path d="M5.5 12h13" stroke="#fff" stroke-width="1.2"/></svg>
      www.larkmoorsite.com
    </li>
    <li class="contacts__item">
      <svg class="contacts__icon" viewBox="0 0 24 24"><circle cx="12" cy="12" r="12" fill="#1f3f8c"/><circle cx="12" cy="12" r="3" fill="none" stroke="#fff" stroke-width="1.6"/><path d="M15 10v3.2c0 1.6 2.6 1.6 2.6-.6A5.7 5.7 0 1 0 15 17.2" fill="none" stroke="#fff" stroke-width="1.6" stroke-linecap="round"/></svg>
      @larkmoordrone
    </li>
    <li class="contacts__item">
      <svg class="contacts__icon" viewBox="0 0 24 24"><circle cx="12" cy="12" r="12" fill="#1f3f8c"/><circle cx="12" cy="12" r="3" fill="none" stroke="#fff" stroke-width="1.6"/><path d="M15 10v3.2c0 1.6 2.6 1.6 2.6-.6A5.7 5.7 0 1 0 15 17.2" fill="none" stroke="#fff" stroke-width="1.6" stroke-linecap="round"/></svg>
      @larkmoordrone
    </li>
  </ul>

  <div class="drone-photo" role="img" aria-label="Photo of a Voskel Ferra Q80 agricultural spray drone with four sprayers"></div>

  <div class="front-rule"></div>
  <div class="front-band">
    Fully Licensed an insured<br>
    RePL 7730152; ReOC 4418; PCR B318207
  </div>
</section>

<section class="card card--back">
  <div class="field-photo" role="img" aria-label="Photo of a Voskel Ferra Q80 drone flying over green crop rows with hills behind"></div>
  <div class="services">SPRAY • WEED • SEED • FEED</div>
  <div class="back-band"></div>
  <div class="brand">
    <div class="brand__name">Larkmoor Drones</div>
    <div class="brand__tagline">SERVICING CENTRAL QUEENSLAND</div>
  </div>
</section>

</body>
</html>
```